Im open to ideas.. I was thinking on my business cards aswell as my logo. a place for my name. email. phone number and abn..

ive attched a file with my business logo. which i dont love the colours.. i was think a dark background with charcoal letters so something along those colour schumes but im open to ideas..

BRM Constructions

```html
<!DOCTYPE html>
<html lang="en">
<head>
<meta charset="utf-8">
<title>BRM Constructions – Business Card</title>
<link href="https://fonts.googleapis.com/css2?family=Open+Sans:wght@400;600;700;800&display=swap" rel="stylesheet">
<style>
  :root {
    --stage: #000000;
    --card-light: #f3f3f3;
    --brand-red: #ec1c24;
    --ink: #231f20;
    --ink-soft: #2b2b2b;
    --white: #ffffff;
  }
  html, body {
    margin: 0;
    padding: 0;
    width: 1200px;
    height: 900px;
    overflow: hidden;
    background: var(--stage);
    font-family: "Open Sans", Arial, sans-serif;
  }
  .canvas {
    position: relative;
    width: 1200px;
    height: 900px;
  }
  .card {
    position: absolute;
    top: 200px;
    width: 310px;
    height: 502px;
    box-sizing: border-box;
  }
  .card-front {
    left: 265px;
    background: var(--card-light);
    border-radius: 58px 0 58px 0;
  }
  .card-back {
    left: 641px;
    width: 309px;
    background: var(--brand-red);
    border-radius: 0 58px 0 58px;
  }
  .wordmark {
    position: absolute;
    text-align: center;
    font-family: "Open Sans", Arial, sans-serif;
    font-weight: 800;
    line-height: 1;
  }
  .wordmark-main {
    display: block;
    font-size: 50px;
    letter-spacing: 4px;
  }
  .wordmark-sub {
    display: block;
    font-size: 11px;
    letter-spacing: 6.2px;
    margin-top: 6px;
    padding-left: 6px;
  }
  .card-front .wordmark {
    left: 30px;
    width: 264px;
    top: 280px;
    top: 82px;
    color: var(--ink);
  }
  .card-back .wordmark {
    left: 22px;
    width: 270px;
    top: 390px;
    color: var(--white);
  }
  .contact-block {
    position: absolute;
    left: 32px;
    top: 318px;
    color: var(--ink-soft);
  }
  .person-name {
    margin: 0;
    font-size: 18px;
    font-weight: 600;
    color: var(--brand-red);
    line-height: 1.2;
  }
  .person-role {
    margin: 1px 0 0;
    font-size: 13px;
    line-height: 1.3;
  }
  .abn {
    margin: 18px 0 0;
    font-size: 13px;
    font-weight: 700;
  }
  .abn-label { color: var(--brand-red); }
  .contact-list {
    list-style: none;
    margin: 14px 0 0;
    padding: 0;
    font-size: 13px;
  }
  .contact-list li {
    display: flex;
    align-items: center;
    height: 21px;
  }
  .contact-icon {
    width: 10px;
    height: 10px;
    margin-right: 7px;
    fill: var(--brand-red);
    flex: none;
  }
</style>
</head>
<body>
<div class="canvas">
  <section class="card card-front">
    <div class="wordmark">
      <span class="wordmark-main">BRM</span>
      <span class="wordmark-sub">CONSTRUCTIONS</span>
    </div>
    <div class="contact-block">
      <p class="person-name">Daniel Carter</p>
      <p class="person-role">Managing Director</p>
      <p class="abn"><span class="abn-label">ABN NO:</span> 12345</p>
      <ul class="contact-list">
        <li>
          <svg class="contact-icon" viewBox="0 0 10 10" aria-hidden="true"><path d="M2 0.5 L3.6 2.6 L2.8 3.6 C3.4 5 4.9 6.5 6.4 7.2 L7.4 6.4 L9.5 8 L8.4 9.5 C4.4 9.2 0.8 5.6 0.5 1.6 Z"/></svg>
          (044)-318-2265
        </li>
        <li>
          <svg class="contact-icon" viewBox="0 0 10 10" aria-hidden="true"><path d="M0.5 2 H9.5 V8.2 H0.5 Z M1.2 2.6 L5 5.4 L8.8 2.6" stroke="#f3f3f3" stroke-width="0.8"/></svg>
          info@youremail.com
        </li>
        <li>
          <svg class="contact-icon" viewBox="0 0 10 10" aria-hidden="true"><circle cx="5" cy="5" r="4.6"/><path d="M2.5 3 C3.5 3.5 4 4.5 3.6 5.6 M6.5 2 C6 3.5 7 4.2 8 4.5 M5 6.5 C5.8 7 6 8 5.8 9" stroke="#f3f3f3" stroke-width="0.8" fill="none"/></svg>
          www.website.com
        </li>
      </ul>
    </div>
  </section>

  <section class="card card-back">
    <div class="wordmark">
      <span class="wordmark-main">BRM</span>
      <span class="wordmark-sub">CONSTRUCTIONS</span>
    </div>
  </section>
</div>
</body>
</html>
```